Medical consulting firm needs polished website

I am a physician and working on setting up a smal consulting firm in New Hampshire, USA. It is called Bright Harbor Medical Services, LLC and the website will be BrightHarborMed.com. I was puttering around at making my own website, and it just didn't come together nicely so I've decided to leave it to the pros. The focus of the business is Advanced Care Planning, ie planning for your future medical needs. So it deals with some heavy stuff like planning for if you get sick, who should make decisions for you, end of life options etc. So it can't be too flippant or cutesy, but also can't be too dour and dark. I am hoping to convey that by thinking ahead and making some plans you can lift some of the worries off of yourself and your family - and that we can help make a scary sounding path more manageable. I want it to be made with wordpress and I have actually already bought a template ( Vitarun – A Modern Multidisciplinary Medical & Health Theme ). The website needs to have general information about our services, doc profile, appointment maker, blog/url link page, and ideally web commerce application ( the template has access to woocommerce). I've posted my business card and current brochure (still tweaking them, but you get the idea). I am also partnering with lumenfold.com and so have included their logo and would want connections/info about them. I have the logos etc in different formats as needed.

Target Market(s)

middle aged to older adults

Industry/Entity Type

Medical

Coding

Coded - Design and coding required

Font styles to use
Sans Serif

Requirements
Must have
• as above.
Nice to have
• Ease of reading/access for elderly viewers. woo commerce.

```html
<!DOCTYPE html>
<html lang="en">
<head>
<meta charset="utf-8">
<title>Bright Harbor Medical Services</title>
<link href="https://fonts.googleapis.com/css2?family=Open+Sans:wght@400;600;700;800&display=swap" rel="stylesheet">
<style>
:root{
  --green:#3aa935;
  --green-bright:#4cc13f;
  --blue:#1e6fbf;
  --blue-dark:#15599d;
  --text:#555;
  --muted:#777;
  --light:#f2f2f2;
  --white:#fff;
  --dark:#333;
}
*{margin:0;padding:0;box-sizing:border-box}
html,body{width:1200px;height:2875px;overflow:hidden}
body{font-family:"Open Sans",Arial,sans-serif;color:var(--text);background:var(--white);position:relative}

/* header */
.site-header{position:absolute;left:0;top:0;width:1200px;height:105px;background:var(--white)}
.brand{position:absolute;left:75px;top:32px;display:flex;align-items:center;gap:12px}
.brand-dot{width:40px;height:40px;border-radius:50%;background:var(--blue)}
.brand-name{font-size:30px;font-weight:600;color:var(--blue);letter-spacing:-.5px}
.contact-block{position:absolute;top:26px;display:flex;gap:14px}
.contact-block svg{margin-top:4px}
.contact-label{font-size:13px;font-weight:700;color:var(--blue);text-transform:uppercase}
.contact-phone{font-size:27px;font-weight:700;color:var(--green);line-height:1.2}
.contact-email{font-size:15px;font-weight:700;color:var(--green);margin-top:6px}

/* nav */
.main-nav{position:absolute;left:0;top:105px;width:1200px;height:60px;background:var(--blue);display:flex;align-items:center;padding-left:83px}
.main-nav a{color:var(--white);font-size:14px;font-weight:700;text-decoration:none;text-transform:uppercase}
.main-nav a + a{margin-left:50px}

/* hero */
.hero{position:absolute;left:0;top:165px;width:1200px;height:500px;overflow:hidden}
.hero-photo{position:absolute;inset:0;background:linear-gradient(90deg,#2f3033 0%,#4a4b4f 35%,#8d959d 62%,#c7ccd1 85%,#e2e5e8 100%)}
.hero-title{position:absolute;left:72px;top:110px;font-size:68px;font-weight:800;color:var(--green-bright);letter-spacing:1px}
.hero-sub{position:absolute;left:76px;top:197px;font-size:26px;font-weight:700;color:var(--white);letter-spacing:.5px}
.btn{display:inline-block;color:var(--white);font-weight:700;text-transform:uppercase;font-size:15px;text-align:center;text-decoration:none}
.btn-green{position:absolute;left:75px;top:255px;width:167px;height:53px;line-height:53px;background:var(--green)}
.hero-dots{position:absolute;left:75px;top:346px;display:flex;gap:8px}
.hero-dots span{width:11px;height:11px;border-radius:50%;background:var(--white)}
.hero-dots span:first-child{background:var(--blue)}
.hero-wave{position:absolute;left:0;bottom:0}

/* section heads */
.section-title{position:absolute;left:0;width:1200px;text-align:center;font-size:31px;font-weight:700;color:var(--green);text-transform:uppercase}
.section-sub{position:absolute;left:0;width:1200px;text-align:center;font-size:17px;color:var(--muted);line-height:26px}

/* services */
.services-band{position:absolute;left:0;top:750px;width:1200px;height:150px;background:linear-gradient(#fff,#e4e4e4)}
.service{position:absolute;top:795px;width:330px}
.service-card{height:195px;border-radius:105px 105px 70px 70px;background:linear-gradient(#fff 0%,#f4f4f4 60%,#e9e9e9 100%);box-shadow:0 8px 0 #dcdcdc;text-align:center;padding-top:38px}
.service-title{margin-top:22px;font-size:18px;font-weight:700;color:var(--blue);text-transform:uppercase;line-height:26px}
.service-text{margin-top:24px;text-align:center;font-size:17px;line-height:26px;color:var(--muted);padding:0 20px}

/* welcome */
.welcome{position:absolute;left:0;top:1130px;width:1200px;height:490px;background:var(--light)}
.welcome-wave{position:absolute;left:0;top:1110px}
.welcome-ring{position:absolute;left:88px;top:1148px;width:345px;height:360px;border-radius:50%;background:var(--green-bright)}
.welcome-photo{position:absolute;left:70px;top:1172px;width:355px;height:370px;border-radius:50%;background:radial-gradient(circle at 45% 45%,#e3b79b 0%,#c99173 18%,#2c84c4 40%,#1b3f66 75%,#111b26 100%)}
.welcome-title{position:absolute;left:525px;top:1286px;font-size:31px;font-weight:700;color:var(--green);text-transform:uppercase}
.welcome-text{position:absolute;left:525px;top:1346px;width:602px;font-size:15px;line-height:25px;color:var(--text)}
.btn-blue{position:absolute;left:525px;top:1500px;width:165px;height:53px;line-height:53px;background:var(--blue)}

/* why choose */
.why{position:absolute;left:0;top:1620px;width:1200px;height:655px;background:#f1f1f1}
.why-card{position:absolute;top:1798px;width:330px;height:420px;background:var(--white);text-align:center}
.why-photo{height:202px}
.photo-family{background:linear-gradient(135deg,#c9a487,#8a6a55 55%,#e8d9cc)}
.photo-care{background:linear-gradient(135deg,#f0e3cf,#d9b79a 45%,#2f6fa5)}
.photo-desk{background:linear-gradient(135deg,#4a4a4a,#9a9a9a 40%,#e9e9e9 80%,#c9503c)}
.why-title{margin-top:30px;font-size:18px;font-weight:700;color:var(--blue);text-transform:uppercase}
.why-text{margin-top:12px;font-size:15px;line-height:26px;color:var(--muted);padding:0 40px}
.why-link{display:block;margin-top:20px;font-size:13px;font-weight:700;color:var(--green);text-transform:uppercase;text-decoration:none}

/* signup */
.signup-input{position:absolute;left:253px;top:2462px;width:513px;height:46px;border:1px solid #dcdcdc;font-family:inherit;font-size:14px;padding-left:14px;color:#999;background:var(--white)}
.signup-btn{position:absolute;left:780px;top:2462px;width:165px;height:46px;line-height:46px;background:var(--blue)}

/* footer */
.site-footer{position:absolute;left:0;top:2528px;width:1200px;height:272px;background:linear-gradient(#e6e6e6,#f6f6f6)}
.footer-brand{position:absolute;left:75px;top:2578px;display:flex;align-items:center;gap:10px}
.footer-brand .brand-dot{width:34px;height:34px}
.footer-brand .brand-name{font-size:26px}
.footer-about{position:absolute;left:75px;top:2645px;width:230px;font-size:14px;line-height:25px;color:var(--dark)}
.footer-head{position:absolute;top:2568px;font-size:15px;font-weight:700;color:var(--blue);text-transform:uppercase}
.footer-links{position:absolute;top:2598px;list-style:none;font-size:14px;line-height:28px;color:var(--dark)}
.footer-info{position:absolute;left:650px;top:2598px;width:220px;font-size:14px;line-height:25px;color:var(--dark)}
.footer-info strong{color:var(--green);font-size:13px;text-transform:uppercase}
.footer-info .row{display:flex;align-items:center;gap:10px;margin-top:6px}
.social{position:absolute;left:905px;top:2604px;display:flex;gap:15px}
.social span{width:18px;height:18px;border-radius:3px;background:#666}
.partner{position:absolute;left:905px;top:2672px;display:flex;align-items:center;gap:10px}
.partner-square{width:14px;height:14px;background:var(--blue)}
.partner-name{font-size:20px;font-weight:700;color:var(--blue)}
.copyright{position:absolute;left:0;top:2800px;width:1200px;height:75px;background:#dadada;text-align:center;line-height:75px;font-size:12px;color:#777}
</style>
</head>
<body>

<header class="site-header">
  <div class="brand"><span class="brand-dot"></span><span class="brand-name">Bright Harbor</span></div>
  <div class="contact-block" style="left:643px">
    <svg width="18" height="18" viewBox="0 0 18 18"><rect width="18" height="18" rx="3" fill="#555"/><path d="M5 4l2 0 1 3-1.5 1a7 7 0 0 0 3.5 3.5L11 10l3 1v2a1 1 0 0 1-1 1A9 9 0 0 1 4 5a1 1 0 0 1 1-1z" fill="#fff"/></svg>
    <div><div class="contact-label">Contact us now:</div><div class="contact-phone">603 555 0142</div></div>
  </div>
  <div class="contact-block" style="left:897px">
    <svg width="22" height="16" viewBox="0 0 22 16"><rect width="22" height="16" rx="2" fill="#555"/><path d="M1 2l10 7 10-7" stroke="#fff" stroke-width="1.6" fill="none"/></svg>
    <div><div class="contact-label">Email us:</div><div class="contact-email">info@brightharbormed.com</div></div>
  </div>
</header>

<nav class="main-nav">
  <a href="#">Home</a><a href="#">About us</a><a href="#">Our service</a><a href="#">Why choose us</a><a href="#">Pricing plans</a><a href="#">Blog</a><a href="#">Testimonials</a><a href="#">Contact us</a>
</nav>

<section class="hero">
  <div class="hero-photo" role="img" aria-label="Photo of a caregiver helping an elderly man walk with a walker"></div>
  <h1 class="hero-title">Bright Harbor</h1>
  <p class="hero-sub">Advanced Care Planning Specialists</p>
  <a class="btn btn-green" href="#">Read more</a>
  <div class="hero-dots"><span></span><span></span><span></span><span></span></div>
  <svg class="hero-wave" width="1200" height="70" viewBox="0 0 1200 70" preserveAspectRatio="none">
    <path d="M0 30 Q600 85 1200 18 L1200 70 L0 70 Z" fill="#fff"/>
    <path d="M0 30 Q600 85 1200 18 L1200 30 Q600 95 0 42 Z" fill="#1e6fbf"/>
  </svg>
</section>

<h2 class="section-title" style="top:712px">Our services</h2>
<div class="services-band"></div>

<div class="service" style="left:75px">
  <div class="service-card">
    <svg width="56" height="46" viewBox="0 0 56 46"><rect x="8" y="4" width="40" height="28" rx="2" fill="none" stroke="#1e6fbf" stroke-width="4"/><rect x="2" y="36" width="52" height="5" rx="2" fill="#1e6fbf"/></svg>
    <div class="service-title">Guided healthcare<br>planning</div>
  </div>
  <p class="service-text">Vestibulum ante ipsum primis in faucibus orci luctus et ultrices posuere cubilia.</p>
</div>
<div class="service" style="left:435px">
  <div class="service-card">
    <svg width="50" height="52" viewBox="0 0 50 52"><circle cx="25" cy="13" r="11" fill="#1e6fbf"/><path d="M4 52c0-15 9-24 21-24s21 9 21 24z" fill="#1e6fbf"/><path d="M17 30v10a4 4 0 0 0 8 0M33 30v8" stroke="#fff" stroke-width="2.5" fill="none"/><circle cx="33" cy="41" r="3" fill="#fff"/></svg>
    <div class="service-title">Shareing your decision<br>with your doctor</div>
  </div>
  <p class="service-text">Vestibulum ante ipsum primis in faucibus orci luctus et ultrices posuere cubilia.</p>
</div>
<div class="service" style="left:793px">
  <div class="service-card">
    <svg width="42" height="50" viewBox="0 0 42 50"><path d="M10 22V14a11 11 0 0 1 22 0v8" stroke="#1e6fbf" stroke-width="5" fill="none"/><rect x="3" y="21" width="36" height="28" rx="3" fill="#1e6fbf"/></svg>
    <div class="service-title">Secure web storage<br>documents</div>
  </div>
  <p class="service-text">Vestibulum ante ipsum primis in faucibus orci luctus et ultrices posuere cubilia.</p>
</div>

<section class="welcome"></section>
<svg class="welcome-wave" width="1200" height="60" viewBox="0 0 1200 60" preserveAspectRatio="none"><path d="M0 0 L1200 0 L1200 45 Q900 0 600 20 Q300 45 0 15 Z" fill="#fff"/><path d="M0 15 Q300 45 600 20 Q900 0 1200 45 L1200 60 L0 60 Z" fill="#f2f2f2"/></svg>
<div class="welcome-ring"></div>
<div class="welcome-photo" role="img" aria-label="Photo of a caregiver holding an elderly person's hand"></div>
<h2 class="welcome-title">Welcome to our website</h2>
<p class="welcome-text">Lorem ipsum dolor sit amet, consectetuer. Proin gravida nibh vel velit auctor aliquet. Aenean sollicitudin, lorem quis bibendum auctor, nisi elit consequat ipsum, nec sagittis sem nibh id elit. Duis sed odio sit amet nibh vulputate cursus a sit amet mauris. Morbi accumsan ipsum velit. Maecenas tempus, tellus eget condimentum rhoncus, sem quam semper libero.</p>
<a class="btn btn-blue" href="#">Read more</a>

<section class="why"></section>
<h2 class="section-title" style="top:1657px">Why choose us</h2>
<p class="section-sub" style="top:1718px">Vestibulum ante ipsum primis in faucibus orci luctus et ultrices<br>posuere cubilia.</p>

<article class="why-card" style="left:75px">
  <div class="why-photo photo-family" role="img" aria-label="Photo of a smiling three-generation family"></div>
  <h3 class="why-title">Lorem ipsum dolor</h3>
  <p class="why-text">Vestibulum ante ipsum primis in faucibus orci luctus et ultrices posuere cubilia.</p>
  <a class="why-link" href="#">Learn more</a>
</article>
<article class="why-card" style="left:435px">
  <div class="why-photo photo-care" role="img" aria-label="Photo of a nurse with an elderly woman"></div>
  <h3 class="why-title">Lorem ipsum dolor</h3>
  <p class="why-text">Vestibulum ante ipsum primis in faucibus orci luctus et ultrices posuere cubilia.</p>
  <a class="why-link" href="#">Learn more</a>
</article>
<article class="why-card" style="left:793px">
  <div class="why-photo photo-desk" role="img" aria-label="Photo of a calculator, stethoscope and paperwork on a desk"></div>
  <h3 class="why-title">Lorem ipsum dolor</h3>
  <p class="why-text">Vestibulum ante ipsum primis in faucibus orci luctus et ultrices posuere cubilia.</p>
  <a class="why-link" href="#">Learn more</a>
</article>

<h2 class="section-title" style="top:2313px">Get our pricing plans</h2>
<p class="section-sub" style="top:2372px">Vestibulum ante ipsum primis in faucibus orci luctus et ultrices<br>posuere cubilia.</p>
<input class="signup-input" type="email" placeholder="Enter Email Address">
<a class="btn signup-btn" href="#">Sign up</a>

<footer class="site-footer"></footer>
<div class="footer-brand"><span class="brand-dot"></span><span class="brand-name">Bright Harbor</span></div>
<p class="footer-about">Lorem ipsum dolor sit amet, consectetuer. Proin gravida nibh vel velit auctor aliquet. Aenean sollicitudin, lorem quis bibendum auctor, nisi elit consequat ipsum.</p>

<h4 class="footer-head" style="left:375px">Company</h4>
<ul class="footer-links" style="left:375px"><li>Home</li><li>About Us</li><li>Our Service</li><li>Why Choose Us</li><li>Pricing Plans</li></ul>
<ul class="footer-links" style="left:507px"><li>Blog</li><li>Testimonials</li><li>Contact Us</li></ul>

<h4 class="footer-head" style="left:650px">Contact info</h4>
<div class="footer-info">
  <strong>Bright Harbor</strong><br>412 Harbor Lane,<br>Concord, NH 03301
  <div class="row"><svg width="12" height="12" viewBox="0 0 18 18"><path d="M5 2l3 0 1 4-2 1.5a8 8 0 0 0 3.5 3.5L12 9l4 1v3a2 2 0 0 1-2 2A12 12 0 0 1 3 4a2 2 0 0 1 2-2z" fill="#555"/></svg>603 555 0142</div>
  <div class="row"><svg width="13" height="10" viewBox="0 0 22 16"><rect width="22" height="16" rx="2" fill="#555"/><path d="M1 2l10 7 10-7" stroke="#fff" stroke-width="2" fill="none"/></svg>info@brightharbormed.com</div>
</div>

<h4 class="footer-head" style="left:905px">Connect us</h4>
<div class="social"><span></span><span></span><span></span><span></span><span></span></div>
<div class="partner"><span class="partner-square"></span><span class="partner-name">Lumenfold</span></div>

<div class="copyright">Copyright © 2016, Company Name, All Right Reserved</div>

</body>
</html>
```